Tiskoro

We need a business card for our company is a holding for different business all are different we try to have some air of relax and fun in our projects we add pictures of the office to give you an idea od the mood of the business

Business

```html
<!DOCTYPE html>
<html lang="en">
<head>
<meta charset="utf-8">
<title>Tiskoro – Business Card</title>
<link rel="stylesheet" href="https://fonts.googleapis.com/css2?family=Exo+2:wght@400;600;800&display=swap">
<style>
  :root {
    --bg: #e9e6e1;
    --card: #ffffff;
    --brown: #6b4a2b;
    --brown-dark: #5a3d22;
    --yellow: #f6e24a;
    --text: #5a3d22;
    --muted: #6d6d6d;
  }
  html, body {
    margin: 0;
    width: 1200px;
    height: 899px;
    overflow: hidden;
    background: var(--bg);
    font-family: "Exo 2", sans-serif;
  }
  .card {
    position: absolute;
    left: 100px;
    top: 170px;
    width: 1000px;
    height: 560px;
    border-radius: 44px;
    overflow: hidden;
    background: var(--card);
    box-shadow: 0 18px 40px rgba(60, 40, 20, 0.18);
  }
  .card-shapes { position: absolute; inset: 0; width: 100%; height: 100%; }
  .brand {
    position: absolute;
    left: 70px;
    top: 110px;
    display: flex;
    align-items: center;
    gap: 16px;
  }
  .brand-square {
    width: 46px;
    height: 46px;
    background: var(--yellow);
  }
  .brand-name {
    font-weight: 800;
    font-size: 64px;
    color: var(--brown-dark);
    letter-spacing: 0.5px;
  }
  .contact {
    position: absolute;
    left: 560px;
    top: 56px;
    color: var(--text);
  }
  .person-name {
    font-size: 28px;
    font-weight: 600;
    letter-spacing: 2px;
    margin: 0;
  }
  .person-role {
    font-size: 17px;
    margin: 2px 0 22px;
    color: var(--muted);
  }
  .address {
    font-size: 19px;
    line-height: 1.3;
    margin: 0 0 24px;
    letter-spacing: 1px;
  }
  .details { list-style: none; margin: 0; padding: 0; }
  .details li {
    display: flex;
    align-items: center;
    gap: 14px;
    font-size: 15px;
    color: var(--muted);
    margin-bottom: 9px;
    letter-spacing: 1px;
  }
  .details svg { width: 16px; height: 16px; fill: var(--brown); }
  .website {
    position: absolute;
    right: 80px;
    bottom: 34px;
    color: #ffffff;
    font-size: 22px;
    letter-spacing: 4px;
  }
</style>
</head>
<body>
  <div class="card">
    <svg class="card-shapes" viewBox="0 0 1000 560" preserveAspectRatio="none">
      <path d="M0 235 C 220 370, 620 425, 1000 405 L1000 560 L0 560 Z" fill="var(--yellow)"/>
      <path d="M0 282 C 230 385, 620 435, 1000 418 L1000 560 L0 560 Z" fill="var(--card)"/>
      <path d="M0 300 C 240 400, 620 445, 1000 425 L1000 560 L0 560 Z" fill="var(--yellow)"/>
      <path d="M0 318 C 250 412, 620 458, 1000 438 L1000 560 L0 560 Z" fill="var(--brown)"/>
    </svg>

    <div class="brand">
      <span class="brand-square"></span>
      <span class="brand-name">Tiskoro</span>
    </div>

    <div class="contact">
      <p class="person-name">MARCUS DELANEY</p>
      <p class="person-role">Managing Director</p>
      <p class="address">041 9th floor Quay<br>Harbour Lane TKR</p>
      <ul class="details">
        <li><svg viewBox="0 0 24 24"><path d="M6.6 10.8a15 15 0 0 0 6.6 6.6l2.2-2.2c.3-.3.7-.4 1-.2 1.1.4 2.3.6 3.6.6.6 0 1 .4 1 1V20c0 .6-.4 1-1 1A17 17 0 0 1 3 4c0-.6.4-1 1-1h3.5c.6 0 1 .4 1 1 0 1.3.2 2.5.6 3.6.1.3 0 .7-.2 1z"/></svg>014 552 3071</li>
        <li><svg viewBox="0 0 24 24"><rect x="6" y="2" width="12" height="20" rx="2"/></svg>014 552 3072</li>
        <li><svg viewBox="0 0 24 24"><rect x="3" y="8" width="18" height="12" rx="1"/><rect x="6" y="3" width="12" height="6"/></svg>014 552 3073</li>
        <li><svg viewBox="0 0 24 24"><path d="M2 5h20v14H2z"/></svg>hello@tiskoro.co</li>
        <li><svg viewBox="0 0 24 24"><circle cx="12" cy="12" r="10"/></svg>www.tiskoro-group.com</li>
      </ul>
    </div>

    <div class="website">www.tiskoro-group.com</div>
  </div>
</body>
</html>
```